IT Company requires new Business Card design.

Over the years we have had a few different business card designs. We are now due for new cards across the board for all staff. We felt this would be a good time to start fresh with a new design. Our traditional card simply had our details on the front, and a list of services on the back. We don't particularly need the list of services, we have had cards where the only thing on the rear of the card was our logo.
Feel free to be creative, we would like our tag line "Complete IT Management" to appear at some point, doesn't necessarily have to be with the logo.
I have attached samples and drafts of various previous cards we have used over the years.

```html
<!DOCTYPE html>
<html lang="en">
<head>
<meta charset="utf-8">
<title>Harbour Networking – Business Card</title>
<link href="https://fonts.googleapis.com/css2?family=Open+Sans:wght@400;700;800&display=swap" rel="stylesheet">
<style>
  :root {
    --backdrop: #e6e6e6;
    --card: #ffffff;
    --brand: #5f6b77;
    --ink: #3a3a3a;
    --ink-soft: #555555;
  }
  * { box-sizing: border-box; margin: 0; padding: 0; }
  html, body {
    width: 1034px;
    height: 1200px;
    overflow: hidden;
    background: var(--backdrop);
    font-family: "Open Sans", Arial, sans-serif;
    color: var(--ink);
  }
  .card {
    position: absolute;
    left: 74px;
    width: 890px;
    height: 515px;
    background: var(--card);
    overflow: hidden;
  }
  .card--front { top: 65px; }
  .card--back { top: 628px; }

  .brand-block {
    position: absolute;
    background: var(--brand);
  }
  .card--front .brand-block { left: 95px; top: 92px; width: 320px; height: 320px; }
  .card--back .brand-block { left: 185px; top: 178px; width: 160px; height: 160px; }

  .tagline {
    position: absolute;
    left: 55px;
    top: 462px;
    width: 400px;
    text-align: center;
    font-size: 17px;
    letter-spacing: 3.5px;
    color: var(--brand);
    text-transform: uppercase;
  }

  .wordmark {
    position: absolute;
    font-weight: 800;
    color: var(--brand);
    line-height: 1;
    text-transform: uppercase;
  }
  .wordmark span { display: block; }
  .card--front .wordmark { left: 512px; top: 40px; }
  .card--front .wordmark .w1 { font-size: 60px; letter-spacing: -1px; }
  .card--front .wordmark .w2 { font-size: 34px; margin-top: 2px; letter-spacing: -0.5px; }
  .card--back .wordmark { left: 378px; top: 196px; }
  .card--back .wordmark .w1 { font-size: 68px; letter-spacing: -1px; }
  .card--back .wordmark .w2 { font-size: 38px; margin-top: 4px; letter-spacing: -0.5px; }

  .person { position: absolute; left: 514px; top: 170px; }
  .person__name { font-size: 26px; font-weight: 700; color: var(--brand); line-height: 1.2; }
  .person__role { font-size: 20px; color: var(--ink-soft); line-height: 1.3; }

  .contacts {
    position: absolute;
    left: 514px;
    top: 246px;
    list-style: none;
  }
  .contacts li {
    display: flex;
    align-items: center;
    height: 33px;
    font-size: 20px;
    color: var(--ink);
    white-space: nowrap;
  }
  .contacts svg { width: 18px; height: 18px; margin-right: 10px; fill: var(--ink-soft); flex: none; }

  .address {
    position: absolute;
    left: 514px;
    top: 430px;
    font-size: 20px;
    line-height: 31px;
    font-style: normal;
    color: var(--ink);
  }

  .site {
    position: absolute;
    left: 0;
    right: 0;
    top: 455px;
    text-align: center;
    font-size: 25px;
    letter-spacing: 1.5px;
    color: var(--ink);
  }
</style>
</head>
<body>

<section class="card card--front">
  <div class="brand-block" aria-hidden="true"></div>
  <p class="tagline">Complete IT Management</p>

  <h1 class="wordmark"><span class="w1">Harbour</span><span class="w2">Networking</span></h1>

  <div class="person">
    <p class="person__name">Daniel Carter</p>
    <p class="person__role">Operation Manager</p>
  </div>

  <ul class="contacts">
    <li>
      <svg viewBox="0 0 20 20" aria-label="Phone"><circle cx="10" cy="10" r="9" fill="none" stroke="#555" stroke-width="1.5"/><path d="M6 5.5l2 -.5 1.2 2.6-1.2 1c.6 1.4 1.6 2.4 3 3l1-1.2 2.6 1.2-.5 2c-4.5 0-8.1-3.6-8.1-8.1z"/></svg>
      08 9000 1470
    </li>
    <li>
      <svg viewBox="0 0 20 20" aria-label="Mobile"><rect x="5" y="1" width="10" height="18" rx="1.5"/><rect x="6.5" y="3" width="7" height="6" fill="#fff"/><rect x="7" y="11" width="6" height="6" fill="#fff" opacity=".5"/></svg>
      0400 118 925
    </li>
    <li>
      <svg viewBox="0 0 20 20" aria-label="Fax"><rect x="5" y="2" width="10" height="6" fill="none" stroke="#555" stroke-width="1.5"/><rect x="1" y="8" width="18" height="8" rx="1.5"/><rect x="5" y="13" width="10" height="5" fill="#fff" stroke="#555" stroke-width="1.2"/></svg>
      08 9000 1470
    </li>
    <li>
      <svg viewBox="0 0 20 20" aria-label="Email"><rect x="1" y="4" width="18" height="12" rx="1.5"/><path d="M1.5 5l8.5 6 8.5-6" fill="none" stroke="#fff" stroke-width="1.5"/></svg>
      dan@harbournetworking.com.au
    </li>
    <li>
      <svg viewBox="0 0 20 20" aria-label="Website"><circle cx="10" cy="10" r="8.5" fill="none" stroke="#555" stroke-width="1.5"/><ellipse cx="10" cy="10" rx="3.5" ry="8.5" fill="none" stroke="#555" stroke-width="1.2"/><path d="M1.5 10h17M3 6h14M3 14h14" stroke="#555" stroke-width="1.2"/></svg>
      www.harbournetworking.com.au
    </li>
  </ul>

  <address class="address">Unit 7 22 Marlow Way<br>Westbrook WA 6170</address>
</section>

<section class="card card--back">
  <div class="brand-block" aria-hidden="true"></div>
  <h2 class="wordmark"><span class="w1">Harbour</span><span class="w2">Networking</span></h2>
  <p class="site">www.harbournetworking.com.au</p>
</section>

</body>
</html>
```